Summit Leadership Studio Roadmap

I've included a mock up of what I like. This design needs to be made better. I like the top section layout. It needs 5 circles for:

Please create a webpage based on this design, but improve it. Use the letterhead and business card brand you created for me to make the brand look seamless.

I love the circles - please make 5 of them the same size (can be 1 lines)

Here is the text for the circles:

Headline: Your Guided Path to Transformation
Text
Step 1: The Initial Consultation
text
Step 2: Deep-Dive Discovery and Assessment
text
Step 3: Synthesis and Strategy Formulation
text
Step 4: The Strategic Debrief Session
Text
Step 5: Implementation and Ongoing Support
Text

Also, there are many sections to this page including:

Introduction
Copy
Copy
Bio
CTA
FAQ's

Please make it interesting.

Use the colors of the mockup and my website: Corwin Adeley.com
I am including my letterhead and business card for brand coherence.

Use the fonts on my website. CorwinAdeley.com

I will need all files to send to the developer. We must have ALL the art files.

see my website; CorwinAdeley.com

See my uploads

Must have
• all the design files

```html
<!DOCTYPE html>
<html lang="en">
<head>
<meta charset="utf-8">
<title>Summit Leadership Studio</title>
<link href="https://fonts.googleapis.com/css2?family=Space+Grotesk:wght@400;500;600&family=Lato:wght@400;700&display=swap" rel="stylesheet">
<style>
:root{
  --navy:#161c45;
  --navy-deep:#121739;
  --gold:#c49a45;
  --gold-soft:#ecdfc0;
  --blue:#2b6b8c;
  --blue-soft:#cfe0e3;
  --cream:#f8f4ec;
  --grey:#eeeef0;
  --ink:#222431;
  --muted:#4a4c58;
  --white:#ffffff;
}
*{box-sizing:border-box;margin:0;padding:0}
html,body{width:1200px;height:4922px;overflow:hidden}
body{font-family:"Lato",sans-serif;color:var(--ink);background:var(--white);position:relative}
.display{font-family:"Space Grotesk",sans-serif;font-weight:500;letter-spacing:.5px}
.abs{position:absolute}
.btn{position:absolute;display:flex;align-items:center;justify-content:center;background:var(--blue);color:var(--white);font-family:"Lato",sans-serif;font-weight:700;font-size:15px;border-radius:22px;text-decoration:none}
.rule{position:absolute;height:4px;width:54px;background:var(--gold)}

/* header */
.site-header{position:absolute;top:0;left:0;width:1200px;height:84px;background:var(--white);z-index:3}
.nav-link{position:absolute;top:32px;font-size:15px;color:var(--ink)}
.nav-link.active{top:27px;height:30px;width:61px;left:111px;background:var(--blue);color:var(--white);border-radius:15px;display:flex;align-items:center;justify-content:center}
.brand-disc{position:absolute;left:472px;top:-90px;width:256px;height:256px;border-radius:50%;background:var(--white);z-index:4;display:flex;flex-direction:column;align-items:center;justify-content:flex-end;padding-bottom:44px}
.brand-mark{width:58px;height:58px;border-radius:50%;background:var(--gold);margin-bottom:12px}
.brand-name{font-family:"Lato",sans-serif;font-weight:700;font-size:16px;color:var(--navy);text-align:center;line-height:1.2}

/* hero */
.hero{position:absolute;top:84px;left:0;width:1200px;height:602px;background:linear-gradient(100deg,#1b2448 0%,#2d3a5c 50%,#4b5672 100%)}
.hero h1{position:absolute;left:111px;top:188px;font-size:56px;line-height:62px;color:var(--white)}
.hero h1 span{color:var(--gold)}
.hero p{position:absolute;left:111px;top:336px;width:540px;font-size:20px;line-height:28px;color:var(--white)}

/* about */
.photo{position:absolute}
.about-title{left:694px;top:796px;font-size:40px;color:var(--ink)}
.about-copy{position:absolute;left:694px;top:900px;width:394px;font-size:14.5px;line-height:26px;color:var(--muted)}
.about-copy p+p{margin-top:26px}

/* path */
.path{position:absolute;top:1362px;left:0;width:1200px;height:610px;background:var(--cream)}
.center-title{position:absolute;left:0;width:1200px;text-align:center;font-size:40px;line-height:48px;color:var(--ink)}
.step{position:absolute;top:280px;width:200px;text-align:center}
.step-ring{position:relative;margin:0 auto;width:180px;height:180px;border-radius:50%;background:var(--gold-soft);display:flex;align-items:center;justify-content:center}
.step-core{width:108px;height:108px;border-radius:50%;background:var(--gold);display:flex;align-items:center;justify-content:center}
.step-num{position:absolute;top:-22px;left:71px;width:38px;height:38px;border-radius:50%;background:var(--navy);color:var(--gold);font-family:"Space Grotesk",sans-serif;font-size:16px;display:flex;align-items:center;justify-content:center}
.step.active .step-ring{background:var(--blue-soft)}
.step.active .step-core{background:var(--blue)}
.step.active .step-num{background:var(--gold);color:var(--white)}
.step-label{margin-top:16px;font-family:"Space Grotesk",sans-serif;font-weight:600;font-size:16px;line-height:19px;color:var(--ink)}
.step-arrow{position:absolute;top:364px;width:24px;height:12px}

/* partner */
.partner{position:absolute;top:1972px;left:0;width:1200px;height:489px;background:linear-gradient(180deg,var(--navy) 0%,#1e2650 100%)}
.partner h2{position:absolute;left:0;top:92px;width:1200px;text-align:center;font-size:40px;line-height:48px;color:var(--gold)}
.partner p{position:absolute;left:200px;top:224px;width:800px;text-align:center;font-size:20px;line-height:28px;color:var(--white)}

/* benefits */
.card{position:absolute;top:2706px;width:309px;text-align:center}
.card .photo{position:relative;width:309px;height:248px}
.card h3{margin-top:20px;font-family:"Space Grotesk",sans-serif;font-weight:500;font-size:21px;line-height:27px;color:var(--gold)}
.card p{margin-top:12px;font-size:14px;line-height:23px;color:var(--muted);padding:0 2px}
.card .btn{position:relative;margin:24px auto 0;width:155px;height:42px}
.slider-arrow{position:absolute;top:2811px;width:34px;height:34px;border-radius:50%;background:var(--blue);display:flex;align-items:center;justify-content:center}

/* bio */
.bio-title{left:111px;top:3302px;font-size:40px;color:var(--ink)}
.bio-copy{position:absolute;left:111px;top:3400px;width:400px;font-size:14.5px;line-height:26px;color:var(--muted);text-align:justify}
.bio-copy p+p{margin-top:26px}

/* faq */
.faq{position:absolute;top:3853px;left:0;width:1200px;height:649px;background:var(--grey)}
.faq-item{position:absolute;width:478px;height:46px;background:var(--white);display:flex;align-items:center;justify-content:space-between;padding:0 20px;font-size:16px;color:var(--ink)}
.faq-plus{width:20px;height:20px;border-radius:50%;background:var(--gold);position:relative}
.faq-plus::before,.faq-plus::after{content:"";position:absolute;background:var(--white);left:5px;top:9px;width:10px;height:2px}
.faq-plus::after{transform:rotate(90deg)}

/* footer */
.site-footer{position:absolute;top:4502px;left:0;width:1200px;height:420px;background:var(--navy-deep);color:var(--white)}
.foot-col{position:absolute;top:84px}
.foot-col h4{font-family:"Lato",sans-serif;font-weight:700;font-size:20px;margin-bottom:22px}
.foot-col li{list-style:none;font-size:14px;line-height:38px;height:38px}
.foot-about{font-size:13.5px;line-height:25px;width:310px}
.foot-contact{display:flex;gap:18px;font-size:14px;line-height:24px;margin-bottom:18px}
.foot-contact svg{flex:none;margin-top:3px}
.foot-social{position:absolute;left:115px;top:253px;width:38px;height:38px;border-radius:6px;background:var(--gold)}
.foot-divider{position:absolute;left:111px;top:377px;width:978px;height:1px;background:rgba(255,255,255,.15)}
.copyright{position:absolute;left:0;top:392px;width:1200px;text-align:center;font-size:12.5px}
</style>
</head>
<body>

<header class="site-header">
  <a class="nav-link active">Home</a>
  <a class="nav-link" style="left:206px">Coaching</a>
  <a class="nav-link" style="left:315px">Retreats</a>
  <a class="nav-link" style="left:822px">About</a>
  <a class="nav-link" style="left:910px">Insights</a>
  <a class="nav-link" style="left:1009px">Contact Us</a>
</header>
<div class="brand-disc">
  <span class="brand-mark"></span>
  <span class="brand-name">Summit Leadership Studio</span>
</div>

<section class="hero" role="img" aria-label="Leader presenting to a seated audience in a conference room">
  <h1 class="display"><span>Summit Leadership</span> for<br>a New Era of Excellence</h1>
  <p>Through personalized guidance, profound insights, and strategic mastery, we help you elevate your impact and create lasting change.</p>
  <a class="btn" style="left:111px;top:461px;width:231px;height:42px">Book a Discovery Call</a>
</section>

<section class="about">
  <div class="photo" role="img" aria-label="Coach speaking to a group of professionals in a bright meeting room" style="left:111px;top:803px;width:487px;height:451px;background:linear-gradient(160deg,#d9dde2 0%,#a9b1bb 55%,#3c4557 100%)"></div>
  <h2 class="display abs about-title">About Us</h2>
  <div class="rule" style="left:694px;top:852px"></div>
  <div class="about-copy">
    <p>Summit Coaching with Corwin Adeley — Your organization—and its challenges—are unlike any other. Generic training can only take your leaders so far. To achieve the profound, lasting impact your vision demands, you need a solution crafted specifically for you.</p>
    <p>Through Summit Coaching, we provide the deep guidance and tailored strategies your leaders need to overcome obstacles, foster unity, and achieve exceptional, lasting results—only possible through a uniquely designed, custom-built program.</p>
  </div>
  <a class="btn" style="left:694px;top:1212px;width:154px;height:42px">Read More</a>
</section>

<section class="path">
  <h2 class="display center-title" style="top:94px">Your Guided<br>Path to Transformation</h2>
  <div class="rule" style="left:573px;top:193px"></div>

  <div class="step" style="left:100px">
    <div class="step-ring"><span class="step-num">01</span><div class="step-core">
      <svg width="46" height="46" viewBox="0 0 46 46" fill="none" stroke="#fff" stroke-width="2"><circle cx="23" cy="13" r="6"/><path d="M12 32c0-6 5-10 11-10s11 4 11 10"/><path d="M6 34h34M10 34v8M36 34v8"/></svg>
    </div></div>
    <div class="step-label">The Initial<br>Consultation</div>
  </div>
  <svg class="step-arrow" style="left:288px" viewBox="0 0 24 12" fill="none" stroke="#b9b4a8" stroke-width="1.5"><path d="M0 6h22M17 1l5 5-5 5"/></svg>

  <div class="step" style="left:300px">
    <div class="step-ring"><span class="step-num">02</span><div class="step-core">
      <svg width="46" height="46" viewBox="0 0 46 46" fill="none" stroke="#fff" stroke-width="2"><rect x="8" y="6" width="26" height="32" rx="2"/><circle cx="24" cy="24" r="8"/><path d="M30 30l8 8"/></svg>
    </div></div>
    <div class="step-label">Deep-Dive Discovery<br>and Assessment</div>
  </div>
  <svg class="step-arrow" style="left:488px" viewBox="0 0 24 12" fill="none" stroke="#b9b4a8" stroke-width="1.5"><path d="M0 6h22M17 1l5 5-5 5"/></svg>

  <div class="step active" style="left:500px">
    <div class="step-ring"><span class="step-num">03</span><div class="step-core">
      <svg width="46" height="46" viewBox="0 0 46 46" fill="none" stroke="#fff" stroke-width="2"><path d="M23 6a11 11 0 0 0-6 20v5h12v-5a11 11 0 0 0-6-20z"/><path d="M18 36h10M20 40h6"/></svg>
    </div></div>
    <div class="step-label">Synthesis and<br>Strategy Formulation</div>
  </div>
  <svg class="step-arrow" style="left:688px" viewBox="0 0 24 12" fill="none" stroke="#b9b4a8" stroke-width="1.5"><path d="M0 6h22M17 1l5 5-5 5"/></svg>

  <div class="step" style="left:700px">
    <div class="step-ring"><span class="step-num">04</span><div class="step-core">
      <svg width="46" height="46" viewBox="0 0 46 46" fill="none" stroke="#fff" stroke-width="2"><path d="M4 22l8-8 8 4 6-4 16 10-8 8-6-4"/><path d="M16 26l8 8M20 22l8 8"/></svg>
    </div></div>
    <div class="step-label">The Strategic<br>Debrief Session</div>
  </div>
  <svg class="step-arrow" style="left:888px" viewBox="0 0 24 12" fill="none" stroke="#b9b4a8" stroke-width="1.5"><path d="M0 6h22M17 1l5 5-5 5"/></svg>

  <div class="step" style="left:900px">
    <div class="step-ring"><span class="step-num">05</span><div class="step-core">
      <svg width="46" height="46" viewBox="0 0 46 46" fill="none" stroke="#fff" stroke-width="2"><circle cx="23" cy="23" r="7"/><path d="M23 6v6M23 34v6M6 23h6M34 23h6M11 11l4 4M31 31l4 4M35 11l-4 4M15 31l-4 4"/></svg>
    </div></div>
    <div class="step-label">Implementation and<br>Ongoing Support</div>
  </div>
</section>

<section class="partner" role="img" aria-label="Dimmed photo of a leadership meeting behind the call to action">
  <h2 class="display">Partner with a<br>Trusted Leadership Advisor</h2>
  <p>Discover the clarity and strategy you need to elevate your leadership performance. From executive presence to organizational influence, your journey starts with a focused consultation.</p>
  <a class="btn" style="left:483px;top:350px;width:232px;height:42px">Book a Discovery Call</a>
</section>

<section class="benefits">
  <h2 class="display center-title" style="top:2550px">Core Benefits of<br>Summit Coaching for Leaders</h2>
  <div class="rule" style="left:573px;top:2652px"></div>

  <div class="slider-arrow" style="left:61px"><svg width="12" height="14" viewBox="0 0 12 14" fill="none" stroke="#fff" stroke-width="2.5"><path d="M9 1L3 7l6 6"/></svg></div>
  <div class="slider-arrow" style="left:1105px"><svg width="12" height="14" viewBox="0 0 12 14" fill="none" stroke="#fff" stroke-width="2.5"><path d="M3 1l6 6-6 6"/></svg></div>

  <article class="card" style="left:111px">
    <div class="photo" role="img" aria-label="Hands joining puzzle pieces together" style="background:linear-gradient(150deg,#2b3140 0%,#5a5f6c 60%,#9a9488 100%)"></div>
    <h3>Exclusivity<br>and Tailored Strategies</h3>
    <p>This is not a one-size-fits-all program. Your coaching experience is designed exclusively for you, your leadership style, and...</p>
    <a class="btn">Read More</a>
  </article>
  <article class="card" style="left:445px">
    <div class="photo" role="img" aria-label="Two colleagues discussing work at a laptop" style="background:linear-gradient(150deg,#c9ccd1 0%,#7c8494 55%,#3d4150 100%)"></div>
    <h3>Navigating<br>Organizational Challenges</h3>
    <p>From internal politics and cultural shifts to external market disruptions, leaders must steer their organizations through...</p>
    <a class="btn">Read More</a>
  </article>
  <article class="card" style="left:778px">
    <div class="photo" role="img" aria-label="Team meeting in a modern office with a presenter" style="background:linear-gradient(150deg,#e6e4e0 0%,#b3b6bb 55%,#5d6270 100%)"></div>
    <h3>Strategic<br>Decision-Making</h3>
    <p>As a leader, you face complex decisions with far-reaching consequences. Summit coaching provides a confidential sounding ...</p>
    <a class="btn">Read More</a>
  </article>
</section>

<section class="bio">
  <h2 class="display abs bio-title">Corwin Adeley</h2>
  <div class="rule" style="left:111px;top:3356px"></div>
  <div class="bio-copy">
    <p>As a top leader, you deserve an elite partnership designed exclusively for you—especially when you need a coach you can count on. With a perspective rooted in both wisdom and empathy, I offer insights, intuition, and support that many other coaches simply cannot replicate.</p>
    <p>My mission is to guide high-performing leaders and their teams toward a state of peak performance defined by stress-free resilience, heightened productivity, and effortless flow.</p>
  </div>
  <a class="btn" style="left:111px;top:3700px;width:155px;height:42px">Read More</a>
  <div class="photo" role="img" aria-label="Portrait of the coach in a dark blazer" style="left:600px;top:3300px;width:487px;height:451px;border-top-right-radius:24px;background:linear-gradient(160deg,#b9bcc0 0%,#6d6a6a 50%,#1f2232 100%)"></div>
</section>

<section class="faq">
  <h2 class="display center-title" style="top:85px">Frequently Asked Questions</h2>
  <div class="rule" style="left:573px;top:145px"></div>
  <div class="faq-item" style="left:111px;top:206px">1. What is Summit Leadership?<span class="faq-plus"></span></div>
  <div class="faq-item" style="left:111px;top:277px">2. Who is this work designed for?<span class="faq-plus"></span></div>
  <div class="faq-item" style="left:111px;top:348px">3. What can I expect from the process?<span class="faq-plus"></span></div>
  <div class="faq-item" style="left:111px;top:420px">4. How do I get started?<span class="faq-plus"></span></div>
  <div class="faq-item" style="left:609px;top:206px">6. What can I expect from the process?<span class="faq-plus"></span></div>
  <div class="faq-item" style="left:609px;top:277px">7. How do I get started?<span class="faq-plus"></span></div>
  <div class="faq-item" style="left:609px;top:348px">8. What is Summit Leadership?<span class="faq-plus"></span></div>
  <div class="faq-item" style="left:609px;top:420px">9. Who is this work designed for?<span class="faq-plus"></span></div>
  <a class="btn" style="left:523px;top:513px;width:154px;height:42px">View All</a>
</section>

<footer class="site-footer">
  <div class="foot-col" style="left:115px">
    <h4>About Us</h4>
    <p class="foot-about">Summit Leadership Studio is a trade name owned by Corwin Adeley International and The Meridian Wellness Institute.</p>
  </div>
  <span class="foot-social"></span>
  <div class="foot-col" style="left:483px">
    <h4>Main Links</h4>
    <ul><li>Home</li><li>Coaching</li><li>Retreats</li><li>About</li><li>Insights</li></ul>
  </div>
  <div class="foot-col" style="left:659px">
    <h4>Contact Us</h4>
    <div class="foot-contact"><svg width="18" height="22" viewBox="0 0 18 22" fill="none" stroke="#fff" stroke-width="1.6"><path d="M9 21s7-7 7-12A7 7 0 0 0 2 9c0 5 7 12 7 12z"/><circle cx="9" cy="9" r="2.5"/></svg><span>1420 Harbor Way, Ste 210<br>#52870 Portland,<br>Oregon 97209-3315</span></div>
    <div class="foot-contact"><svg width="18" height="18" viewBox="0 0 18 18" fill="none" stroke="#fff" stroke-width="1.6"><path d="M3 1h4l2 5-3 2a10 10 0 0 0 4 4l2-3 5 2v4a2 2 0 0 1-2 2A15 15 0 0 1 1 3a2 2 0 0 1 2-2z"/></svg><span>503-555-0148</span></div>
    <div class="foot-contact"><svg width="18" height="14" viewBox="0 0 18 14" fill="none" stroke="#fff" stroke-width="1.6"><rect x="1" y="1" width="16" height="12" rx="1"/><path d="M1 2l8 6 8-6"/></svg><span>corwin@corwinadeley.com</span></div>
  </div>
  <div class="foot-col" style="left:978px">
    <h4>Other Links</h4>
    <ul><li>Membership</li><li>2026 Retreat</li><li>Contact Us</li><li>Terms &amp; Policies</li><li>Privacy Policy</li></ul>
  </div>
  <div class="foot-divider"></div>
  <p class="copyright">Copyright © 2025 Summit Leadership Studio . All rights reserved.</p>
</footer>

</body>
</html>
```